VENTURE CAPITAL GROUP BUSINESS CARD DESIGN

Venture Capital Group based in SF looking for a bold business card design. No trendy colour explosion, 3D effects etc. Just "simple" optical effects. Works on your brain, keeps your eye focused and sticks to your mind.
Target Market(s)
Technology startups
Industry/Entity Type
Venture Capital
Contact Information for Business Card
DESMOND WHITLAKE
MANAGING PARTNER
187 FENWORTH ST SAN FRANCISCO, CA 94187
415.555.0142 O
415.555.0147 F
415.555.0193 C
desmond@veldtmoorcapital.ventures

```html
<!DOCTYPE html>
<html lang="en">
<head>
<meta charset="utf-8">
<title>Veldtmoor Capital Group – Business Card</title>
<link href="https://fonts.googleapis.com/css2?family=Open+Sans:ital,wght@0,400;0,600;1,400&family=Arimo&display=swap" rel="stylesheet">
<style>
  :root {
    --page: #f3f4f1;
    --card: #ffffff;
    --green: #2e8b1c;
    --green-deep: #17740a;
    --green-bright: #3fb524;
    --steel: #9aa6ab;
    --mist: #dfe2dc;
    --mist-light: #eceee9;
    --white: #ffffff;
  }
  * { margin: 0; padding: 0; box-sizing: border-box; }
  html, body { width: 995px; height: 1200px; overflow: hidden; background: var(--page); }
  body { position: relative; font-family: "Open Sans", sans-serif; }

  .card {
    position: absolute;
    left: 50px;
    width: 892px;
    background: var(--card);
    overflow: hidden;
    border: 1px solid #d6d9d3;
  }
  .card--front { top: 49px; height: 521px; }
  .card--back { top: 604px; height: 526px; }

  /* front */
  .brand-disc {
    position: absolute; left: 371px; top: 37px;
    width: 164px; height: 164px; border-radius: 50%;
    background: radial-gradient(circle at 40% 35%, #ffffff 0%, #eef0ee 60%, #d9dcd9 100%);
  }
  .brand-name {
    position: absolute; left: 0; right: 0; top: 218px;
    text-align: center; color: var(--green);
    font-weight: 400; font-size: 48px; letter-spacing: 1px; line-height: 1;
    padding-left: 24px;
  }
  .brand-sub {
    position: absolute; left: 0; right: 0; top: 270px;
    text-align: center; color: var(--green);
    font-weight: 400; font-size: 12px; letter-spacing: 7px; line-height: 1;
    padding-left: 30px;
  }
  .person {
    position: absolute; left: 0; right: 0; top: 294px;
    text-align: center; color: var(--green); padding-left: 24px;
  }
  .person__name { font-size: 21px; line-height: 26px; }
  .person__title { font-size: 19px; line-height: 24px; font-style: italic; }

  .rule { position: absolute; left: 0; right: 0; top: 355px; height: 13px; background: var(--steel); }
  .contact-band {
    position: absolute; left: 0; right: 0; top: 371px; bottom: 0;
    background: radial-gradient(circle at 30% 40%, var(--green-bright), var(--green) 75%);
  }
  .contact-lines {
    position: absolute; left: 50px; top: 386px;
    font-family: "Arimo", sans-serif; font-size: 22px; line-height: 27px; color: var(--white);
  }
  .contact-web {
    position: absolute; right: 44px; top: 446px; text-align: right;
    font-size: 22px; line-height: 26px; color: var(--white);
  }

  /* back */
  .back-field {
    position: absolute; inset: 0;
    background: linear-gradient(180deg, var(--mist-light), var(--mist));
  }
  .back-disc {
    position: absolute; left: 333px; top: 56px;
    width: 278px; height: 278px; border-radius: 50%;
    background: radial-gradient(circle at 45% 40%, rgba(255,255,255,0.95), rgba(255,255,255,0.55) 65%, rgba(255,255,255,0) 100%);
  }
  .back-name {
    position: absolute; left: 333px; top: 170px; width: 278px;
    text-align: center; color: var(--green); font-size: 40px; line-height: 50px;
  }
  .back-band {
    position: absolute; left: 0; right: 0; top: 357px; height: 100px;
    background: var(--green-deep);
    display: flex; flex-direction: column; justify-content: center; align-items: center;
    color: var(--white); font-size: 31px; line-height: 38px;
  }
  .back-swoosh { position: absolute; left: 0; top: 457px; }
</style>
</head>
<body>
  <section class="card card--front">
    <div class="brand-disc"></div>
    <div class="brand-name">VELDTMOOR</div>
    <div class="brand-sub">CAPITAL GROUP</div>
    <div class="person">
      <p class="person__name">DESMOND WHITLAKE</p>
      <p class="person__title">Managing Partner</p>
    </div>
    <div class="rule"></div>
    <div class="contact-band" role="img" aria-label="Green band with concentric circle pattern"></div>
    <div class="contact-lines">
      <p>187 Fenworth st.&nbsp; San francisco, CA 94187</p>
      <p>415.555.0142 O</p>
      <p>415.555.0147 F</p>
      <p>415.555.0193 C</p>
    </div>
    <div class="contact-web">
      <p>desmond@veldtmoorcapital.ventures</p>
      <p>www.veldtmoorcapital.com</p>
    </div>
  </section>

  <section class="card card--back">
    <div class="back-field" role="img" aria-label="Light grey concentric circle pattern background"></div>
    <div class="back-disc"></div>
    <div class="back-name">VELDTMOOR</div>
    <div class="back-band">
      <p>desmond@veldtmoorcapital.ventures</p>
      <p>www.veldtmoorcapital.com</p>
    </div>
    <svg class="back-swoosh" width="892" height="69" viewBox="0 0 892 69" aria-hidden="true">
      <rect x="0" y="0" width="892" height="6" fill="#ffffff"/>
      <path d="M0 8 H892 V69 H790 C600 56 320 30 0 26 Z" fill="var(--green-deep)"/>
    </svg>
  </section>
</body>
</html>
```